"Word Cloud" lists of countries, by decade, who have adopted women's suffrage

The winning designer will (eventually, but not necessarily within this project--see "Nice to Haves", below) design a total of eight images, based on the eight lists of countries (see attached files) in order, by decade, that they adopted women's suffrage.

One of the the attached images is a screen shot of five pages of the book RISE: The Argument for The Realm of Stars, showing how these lists are presently arranged on 6"x9" pages.

We essentially want to spice up these 8 lists and make them more fun to look at, for the reader.

Target Market(s)

General audience. People who want to make a difference. People who want to do something to change the world, and want to read a book about how we can actually do it.

Industry/Entity Type

Political

Font styles to use
Serif
Sans Serif
Decorative
Script

Requirements
Must have
• At least two initial designs, one for each of the two largest lists (lists 5 and 6). All country names must be spelled correctly. A WORD doc has been provided with all the text you need to work with. An EXAMPLE word cloud has been provided for inspiration. The look and feel of these "Country Clouds" wants to go all over the place, but all names should be (at least somewhat) readable.
• IMPORTANT ELEMENTS: (1) There are a few places where current countries were just one, when they got women's suffrage. Keep this info intact, together, in the cloud. EXAMPLE (from list 6):
•  British Leeward Islands (remove ", including today’s:", but keep together with)
•  Antigua and Barbuda
•  British Virgin Islands
•  Montserrat
•  Saint Kitts and Nevis
•  Anguilla
• (2) The names of the countries should stay in roughly the same order as found in the lists, but laid out (very) roughly right to left and then top to bottom, loosely akin to the standard flow of text written in the latin alphabet. It is fine to alter this standard in minor ways to achieve a better look to the design. Just don't move a country found at the top of one list into the middle of that list or down to the bottom, etc.
• These country clouds will be printed in black and white, so keep the designs greyscale.
• These "country clouds" should be 4.5" in width.The largest country clouds, with the most countries found in them, should not exceed 6" in length.
Nice to have
• (Eventually) all 8 lists in the form of "Country Clouds"---that are playful, but with serious elements. Pull up a list of countries by population, have the 20 biggest use the biggest font sizes. Use many different fonts, mix it up! Essentially, these 8 lists all want to become word clouds, with each nation's full name as its own "word." See example cloud.
• Though having all 8 lists in clouds at the end of this project is "nice to have," the winner for this design might simply produce 2 such clouds, along with a cost estimate attached to the submitted design for what they would charge to complete the other 6 clouds.
Should not have
• Do NOT include the textual transitions found between the lists, in the screen shot or word doc. They are there just to help you see how the different graphics will be used and what will go either before or after them.
• No need to use bullet points.

```html
<!DOCTYPE html>
<html lang="en">
<head>
<meta charset="utf-8">
<title>Country Cloud</title>
<link rel="stylesheet" href="https://fonts.googleapis.com/css2?family=Alfa+Slab+One&family=Big+Shoulders+Inline+Display:wght@500&family=Playfair+Display:wght@900&family=Chango&family=Abril+Fatface&family=Oswald:wght@500&family=Bevan&family=Russo+One&family=Cinzel:wght@400&family=Stardos+Stencil:wght@700&display=swap">
<style>
  :root {
    --bg-centre: #ffffff;
    --bg-edge: #dcdcdd;
    --ink-dark: #3f3f40;
    --ink-charcoal: #4a4a4b;
    --ink-slate: #5a5a5c;
    --ink-mid: #808184;
    --ink-soft: #8c8d8f;
    --ink-light: #a7a8aa;
    --rule: #9a9a9c;
  }
  html, body {
    margin: 0;
    padding: 0;
    width: 985px;
    height: 1200px;
    overflow: hidden;
  }
  .country-cloud {
    display: block;
    width: 985px;
    height: 1200px;
    background: radial-gradient(ellipse 60% 55% at 50% 48%, var(--bg-centre) 0%, var(--bg-edge) 100%);
  }
  .country { dominant-baseline: alphabetic; }
  .pitcairn   { font-family: "Alfa Slab One", serif; font-size: 46px; fill: var(--ink-charcoal); }
  .isle-of-man{ font-family: "Big Shoulders Inline Display", sans-serif; font-weight: 500; font-size: 176px; fill: var(--ink-slate); }
  .denmark    { font-family: "Playfair Display", serif; font-weight: 900; font-size: 50px; fill: var(--ink-slate); }
  .cook       { font-family: "Chango", sans-serif; font-size: 74px; fill: var(--ink-light); }
  .new-zealand{ font-family: "Alfa Slab One", serif; font-size: 76px; fill: var(--ink-mid); }
  .australia  { font-family: "Abril Fatface", serif; font-size: 128px; fill: var(--ink-dark); }
  .norway     { font-family: "Oswald", sans-serif; font-weight: 500; font-size: 70px; fill: var(--ink-soft); }
  .finland    { font-family: "Bevan", serif; font-size: 120px; fill: var(--ink-soft); }
  .greenland  { font-family: "Russo One", sans-serif; font-size: 98px; fill: var(--ink-slate); }
  .faroe      { font-family: "Cinzel", serif; font-size: 84px; fill: var(--ink-charcoal); }
  .iceland    { font-family: "Stardos Stencil", sans-serif; font-weight: 700; font-size: 146px; fill: var(--ink-mid); }
  .frame, .rule { fill: none; stroke: var(--rule); stroke-width: 1; }
</style>
</head>
<body>
<svg class="country-cloud" width="985" height="1200" viewBox="0 0 985 1200" xmlns="http://www.w3.org/2000/svg">
  <text class="country pitcairn" x="176" y="180" textLength="644" lengthAdjust="spacingAndGlyphs">THE PITCAIRN ISLANDS</text>
  <text class="country isle-of-man" x="154" y="328" textLength="666" lengthAdjust="spacingAndGlyphs">ISLE OF MAN</text>
  <text class="country denmark" transform="translate(834 138) rotate(90)" x="0" y="0" textLength="274" lengthAdjust="spacingAndGlyphs">DENMARK</text>
  <text class="country cook" x="152" y="400" textLength="652" lengthAdjust="spacingAndGlyphs">COOK ISLANDS</text>
  <text class="country new-zealand" x="164" y="488" textLength="700" lengthAdjust="spacingAndGlyphs">NEW ZEALAND</text>
  <text class="country australia" x="150" y="600" textLength="730" lengthAdjust="spacingAndGlyphs">AUSTRALIA</text>
  <text class="country norway" transform="translate(192 976) rotate(-90)" x="0" y="0" textLength="352" lengthAdjust="spacingAndGlyphs">NORWAY</text>
  <text class="country finland" x="252" y="724" textLength="608" lengthAdjust="spacingAndGlyphs">FINLAND</text>
  <rect class="frame" x="250" y="736" width="614" height="192"/>
  <text class="country greenland" x="264" y="828" textLength="560" lengthAdjust="spacingAndGlyphs">GREENLAND</text>
  <text class="country faroe" x="276" y="908" textLength="564" lengthAdjust="spacingAndGlyphs">Farce Islands</text>
  <text class="country iceland" x="240" y="1040" textLength="624" lengthAdjust="spacingAndGlyphs">ICELAND</text>
  <line class="rule" x1="244" y1="1048.5" x2="866" y2="1048.5"/>
</svg>
</body>
</html>
```